Corporate Design für Lunavello - innovatives Unternehmen im Bereich App-Entwicklung und Kultur
Zielgruppe
Gegenstand des Unternehmens ist:
- Entwurf, Entwicklung und Vermarktung von Soziale Netzwerk-Apps für Unternehmen im Kultursektor und für einzelne Kunstprojekte
- Beratung von Kultureinrichtungen
- Technische Umsetzung als Dienstleister von digitalen Apps, Websites, Softwares für den Kulturbereich
- Entwicklung und Erstellung von digitalen Diensten im Kulturbereich
- Entwicklung von Augmented Reality und 3D Technologien für mobile Devices
- Ausbildung im Bereich Kultur und Kreativität
- Erbringung von Dienstleistungen im Media- und Marketingbereich
- Organisation von Kulturveranstaltungen
Zielgruppe sind insbesondere Kreative und Kultureinrichtungen.
www.lunavello.eu
Aufgabenstellung
bitte die Farbe der Website NICHT berücksichtigen. Wir wollen sowieso die Website ändern.
bitte keine Fernseher, Kameras, Videokameras im Logo. Wir bevorzugen etwas abstraktes.
Danke und viel Spass!!

```html
<!DOCTYPE html>
<html lang="en">
<head>
<meta charset="utf-8">
<title>Lunavello</title>
<link href="https://fonts.googleapis.com/css2?family=Mulish:wght@400;600;700&family=Tinos&display=swap" rel="stylesheet">
<style>
  :root {
    --brand: #e2045e;
    --white: #ffffff;
    --page-bg: #ecf0f1;
    --rule: #e4e4e4;
    --title: #4a4a4a;
    --meta: #c9c9c9;
    --notice-text: #333333;
    --button-bg: #f3f3f3;
    --button-border: #dddddd;
  }
  * { box-sizing: border-box; margin: 0; padding: 0; }
  html, body { width: 1200px; height: 1200px; overflow: hidden; }
  body { position: relative; background: var(--page-bg); font-family: "Mulish", sans-serif; }

  .site-header {
    position: absolute; left: 0; top: 0; width: 1200px; height: 562px;
    background: var(--white);
    display: flex; flex-direction: column; align-items: center; justify-content: center;
  }
  .brand-mark { display: flex; flex-direction: column; align-items: center; gap: 22px; margin-top: 8px; }
  .brand-dot { width: 46px; height: 46px; border-radius: 50%; background: var(--brand); }
  .brand-name {
    color: var(--brand); font-weight: 600; font-size: 24px; letter-spacing: 3.5px;
    text-transform: uppercase;
  }

  .main-nav {
    position: absolute; left: 0; top: 562px; width: 1200px; height: 72px;
    background: var(--white); border-top: 1px solid var(--rule); border-bottom: 1px solid var(--rule);
    display: flex;
  }
  .nav-brand {
    width: 536px; height: 72px; background: var(--brand);
    display: flex; align-items: center; gap: 9px; padding-left: 46px;
  }
  .nav-brand-dot { width: 15px; height: 15px; border-radius: 50%; background: var(--white); }
  .nav-brand-name { color: var(--white); font-size: 10px; font-weight: 600; letter-spacing: 1.4px; text-transform: uppercase; }
  .nav-menu { margin-left: auto; display: flex; list-style: none; height: 72px; }
  .nav-item {
    display: flex; align-items: center; justify-content: center; gap: 6px;
    border-left: 1px solid var(--rule);
    color: var(--brand); font-size: 12px; font-weight: 600; letter-spacing: 2px; text-transform: uppercase;
  }
  .nav-item.education { width: 121px; }
  .nav-item.projects { width: 134px; }
  .nav-item.about { width: 101px; }
  .nav-item.who { width: 92px; }
  .nav-item svg { width: 8px; height: 6px; }

  .post-card {
    position: absolute; top: 690px; width: 556px; height: 560px;
    background: var(--white); border-radius: 3px; overflow: hidden;
  }
  .post-card.left { left: 30px; }
  .post-card.right { left: 614px; }
  .post-image { width: 100%; height: 370px; }
  .post-image.warm { background: linear-gradient(120deg, #c9783a 0%, #a85a2a 45%, #3a2117 100%); }
  .post-image.light { background: linear-gradient(100deg, #8a8266 0%, #d8cfb4 45%, #e8c98a 70%, #b88a45 100%); }
  .post-body { padding: 30px 43px 0; }
  .post-title { color: var(--title); font-weight: 400; font-size: 24px; line-height: 1.3; }
  .post-date { margin-top: 6px; color: var(--meta); font-size: 12px; font-weight: 700; letter-spacing: 2px; text-transform: uppercase; }

  .cookie-notice {
    position: absolute; left: 13px; top: 1138px; width: 1174px; height: 49px;
    background: var(--white); border: 1px solid var(--rule);
    display: flex; align-items: center; justify-content: space-between; padding: 0 10px 0 13px;
    font-family: "Tinos", serif; color: var(--notice-text);
  }
  .cookie-text { font-size: 13px; line-height: 1.3; }
  .cookie-text a { color: var(--notice-text); text-decoration: underline; }
  .cookie-button {
    font-family: "Tinos", serif; font-size: 15px; letter-spacing: 1.5px; color: var(--notice-text);
    background: var(--button-bg); border: 1px solid var(--button-border); border-radius: 3px;
    padding: 8px 12px;
  }
</style>
</head>
<body>
  <header class="site-header">
    <div class="brand-mark">
      <span class="brand-dot"></span>
      <span class="brand-name">Lunavello</span>
    </div>
  </header>

  <nav class="main-nav">
    <div class="nav-brand">
      <span class="nav-brand-dot"></span>
      <span class="nav-brand-name">Lunavello</span>
    </div>
    <ul class="nav-menu">
      <li class="nav-item education">Education
        <svg viewBox="0 0 8 6"><path d="M1 1 L4 4 L7 1" fill="none" stroke="#e2045e" stroke-width="1.6"/></svg></li>
      <li class="nav-item projects">Projects
        <svg viewBox="0 0 8 6"><path d="M1 1 L4 4 L7 1" fill="none" stroke="#e2045e" stroke-width="1.6"/></svg></li>
      <li class="nav-item about">About</li>
      <li class="nav-item who">Who?</li>
    </ul>
  </nav>

  <article class="post-card left">
    <div class="post-image warm" role="img" aria-label="Photo of a dancer speaking into a microphone during an interview in front of a perforated wooden wall"></div>
    <div class="post-body">
      <h2 class="post-title">Tanzsommer Nord: Interview with Quiet Lantern</h2>
    </div>
  </article>

  <article class="post-card right">
    <div class="post-image light" role="img" aria-label="Photo of a choreographer holding a microphone beside glass plant terrariums"></div>
    <div class="post-body">
      <h2 class="post-title">Tanzsommer Nord: Interview with Lena Hartwig</h2>
      <p class="post-date">September 18, 2016</p>
    </div>
  </article>

  <aside class="cookie-notice">
    <p class="cookie-text">Privacy &amp; Cookies: This site uses cookies from Pressfold.com and selected partners.<br>
      To find out more, as well as how to remove or block these, see here: <a>Our Cookie Policy</a></p>
    <span class="cookie-button">Close and accept</span>
  </aside>
</body>
</html>
```